Lone Star Wetland Flora Stewardship Guild

We need to design the home page of this new website. We would like a fun website design for provides as a resource for members and information for potential members.
Please design so that we can see a portion of background on each side on the website.
I just need the final design files psd no coding needed.
Attached is their logo (colors are not 100% set in stone either so can mess with those as I did in the quick mockup attached)
Attached is a pdf newsletter they send out, you can get a feel for them and what they are about. The design is crappy and we are here to fix that going forward and we are starting with the website.
Here are some quick example websites (design style is open)
- I attached a quick mockup i did just for a content visual but by all means do what you want.
- http://www.brightpathleaders.example/
- http://www.civicunityhub.example/
- http://preview.webskinvault.example/show.php?cat=layouts&host=skinbazaar&temp=novaline
- http://www.meadowkeep.example/
- http://www.urbangleaners.example/
- http://www.projectcozyknit.example/
here are some of the other chapters website (pretty bad!)
and here are some of the others:
- http://www.dwrvcs.example/
- http://kwfg.example/
- http://www.blvcg.example/
Content Items that need to be included:
1. Logo
2. Menu - home, about, members, resources, events, membership, contact
3. Become a member - button or action
4. social links - chatterloop, workweave, clipstream
5. banner - that needs to explain their purpose "Promoting environmental stewardship through operations, research, education and outreach" (or this can be worked into the design)
6. Upcoming event (s)
7. Advertisement - members can place an ad on the website, this can be a placeholder for now
8. newsletter signup
9. advertise with us - this link can be in the footer
30-60 years of age, succesfull (household budgets of 120K+ men and women that live in texas.
Education

```html
<!DOCTYPE html>
<html lang="en">
<head>
<meta charset="utf-8">
<title>Lone Star Wetland Flora Stewardship Guild</title>
<link rel="stylesheet" href="https://fonts.googleapis.com/css2?family=Raleway:ital,wght@0,400;0,500;0,600;0,700;1,400&family=Open+Sans:ital,wght@0,400;0,700;1,400&family=Source+Sans+3:wght@400;600&display=swap">
<style>
  :root {
    --navy: #07174a;
    --navy-deep: #03103a;
    --nav-top: #0d2c6e;
    --berry: #a0284a;
    --berry-dark: #8a1f3e;
    --heading-red: #9e2a4c;
    --event-blue: #0e2a66;
    --ink: #222222;
    --body: #333333;
    --white: #ffffff;
    --panel-line: #b9506c;
    --button-dark: #1c1c1c;
  }
  * { box-sizing: border-box; margin: 0; padding: 0; }
  html, body { width: 1200px; height: 1149px; overflow: hidden; }
  body { position: relative; font-family: "Open Sans", Arial, sans-serif; color: var(--body); background: var(--navy); }

  .backdrop {
    position: absolute; inset: 0;
    background:
      linear-gradient(180deg, #c9dcf0 0%, #a9c7e8 14%, #d6e6f2 26%, #7fa26a 36%, #5b7f86 46%, #3e6495 54%, #2b4d8a 60%, #0c1f55 68%, var(--navy) 75%, var(--navy) 100%);
  }

  .abs { position: absolute; }

  .site-title { left: 300px; top: 20px; width: 500px; text-align: right; font-family: "Raleway", sans-serif; font-size: 21px; font-weight: 500; color: #111; white-space: nowrap; }

  .login { left: 812px; top: 21px; width: 92px; height: 31px; border-radius: 5px; background: linear-gradient(180deg, #4a4a4a, #111); color: var(--white); font-family: "Raleway", sans-serif; font-weight: 600; font-size: 16px; letter-spacing: .5px; display: flex; align-items: center; justify-content: center; border: 1px solid #000; }

  .social { left: 914px; top: 27px; display: flex; gap: 9px; font-family: "Open Sans", sans-serif; font-size: 11px; font-weight: 700; color: var(--navy); }
  .social span { display: flex; align-items: center; gap: 3px; }
  .social i { width: 7px; height: 7px; border-radius: 50%; background: var(--berry); display: inline-block; }

  .brand { left: 100px; top: 52px; width: 250px; display: flex; align-items: center; gap: 10px; font-family: "Raleway", sans-serif; font-weight: 700; font-size: 20px; line-height: 24px; color: var(--navy); }
  .brand i { flex: none; width: 16px; height: 16px; border-radius: 50%; background: var(--berry); }

  .main-nav { left: 355px; top: 73px; width: 743px; height: 56px; border-radius: 18px; background: linear-gradient(180deg, var(--nav-top), var(--navy-deep)); display: flex; align-items: center; justify-content: space-between; padding: 0 24px 0 29px; }
  .main-nav a { color: var(--white); text-decoration: none; font-family: Arial, Helvetica, sans-serif; font-size: 15px; }

  .hero { left: 104px; top: 177px; width: 996px; height: 428px; background: var(--white); border: 1px solid #dcdcdc; }
  .hero-photo { left: 11px; top: 11px; width: 666px; height: 402px; background: linear-gradient(180deg, #dfeaf6 0%, #b6d0ec 22%, #4d8a3a 38%, #2f5a2c 50%, #3a5470 60%, #6a7f5a 75%, #2d3a20 100%); }
  .tagline { left: 11px; top: 29px; width: 666px; text-align: center; font-family: "Raleway", sans-serif; font-size: 26px; line-height: 34px; color: #111; }

  .newsletter { left: 677px; top: 11px; width: 305px; height: 402px; background: var(--berry); color: var(--white); }
  .newsletter h2 { position: absolute; left: 18px; top: 23px; font-family: "Raleway", sans-serif; font-weight: 500; font-size: 30px; }
  .newsletter .rule { position: absolute; left: 0; right: 0; height: 1px; background: var(--panel-line); }
  .newsletter p { position: absolute; left: 18px; top: 80px; width: 268px; font-family: Arial, sans-serif; font-size: 14px; line-height: 20px; text-align: justify; }
  .field { position: absolute; left: 20px; width: 261px; height: 34px; background: var(--white); color: #333; font-family: "Open Sans", sans-serif; font-size: 13px; padding-left: 8px; display: flex; align-items: center; border: 1px solid #ddd; }
  .sign-up { position: absolute; left: 149px; top: 243px; width: 132px; height: 34px; border-radius: 4px; background: linear-gradient(180deg, #fdfdfd, #c7c7c7); color: #222; font-family: "Raleway", sans-serif; font-size: 20px; font-weight: 500; display: flex; align-items: center; justify-content: center; border: 1px solid #999; }
  .become { position: absolute; left: 44px; top: 325px; width: 221px; height: 47px; border-radius: 6px; background: linear-gradient(180deg, #3c3c3c, #080808); border: 1px solid #000; color: var(--white); font-family: "Open Sans", sans-serif; font-size: 17px; font-weight: 600; display: flex; align-items: center; justify-content: center; letter-spacing: .3px; }

  .content { left: 104px; top: 655px; width: 996px; height: 425px; background: var(--white); }
  .section-title { position: absolute; font-family: "Raleway", sans-serif; font-size: 30px; font-weight: 400; color: var(--heading-red); }

  .about-text { position: absolute; left: 15px; top: 73px; width: 292px; font-family: "Source Sans 3", sans-serif; font-size: 15.5px; line-height: 22px; color: var(--ink); }
  .read-more { position: absolute; left: 14px; top: 312px; width: 107px; height: 28px; border-radius: 3px; background: #2a2a2a; color: var(--white); font-family: "Open Sans", sans-serif; font-weight: 700; font-size: 14px; display: flex; align-items: center; justify-content: center; }

  .event { position: absolute; left: 348px; width: 330px; height: 66px; }
  .event .thumb { position: absolute; left: 0; top: 0; width: 96px; height: 64px; background: linear-gradient(180deg, #cfe0f2 0%, #8fb3de 30%, #4f8a3a 48%, #3a5f6c 66%, #8a9a4a 100%); }
  .event h3 { position: absolute; left: 110px; top: 0; font-family: "Open Sans", sans-serif; font-weight: 700; font-size: 14.5px; color: var(--event-blue); white-space: nowrap; }
  .event .date { position: absolute; left: 110px; top: 19px; font-style: italic; font-size: 14px; color: var(--berry); }
  .event .blurb { position: absolute; left: 111px; top: 36px; width: 210px; font-size: 13.5px; line-height: 18px; color: var(--ink); }
  .view-all { position: absolute; left: 600px; top: 352px; font-weight: 700; font-size: 14px; color: var(--ink); }

  .ad-slot { position: absolute; left: 704px; top: 19px; width: 276px; height: 357px; background: linear-gradient(180deg, #3c9fc9 0%, #1e6f97 40%, #101418 58%, #1a1a1a 78%, #d9d9d9 79%, #e4e4e4 100%); }

  .copyright { left: 105px; top: 1106px; font-family: Arial, sans-serif; font-size: 14px; color: var(--white); }
  .advertise { left: 971px; top: 1106px; font-family: Arial, sans-serif; font-size: 16px; color: var(--white); text-decoration: underline; }
</style>
</head>
<body>
  <div class="backdrop" role="img" aria-label="Background photo of a sunny Texas lake with lily pads, trees and blue sky"></div>

  <header>
    <div class="abs site-title">Lone Star Wetland Flora Stewardship Guild</div>
    <div class="abs login">LOGIN</div>
    <div class="abs social">
      <span><i></i>chatterloop</span>
      <span><i></i>workweave</span>
      <span><i></i>clipstream</span>
    </div>
    <div class="abs brand"><i></i><span>Lone Star Wetland Flora Stewardship Guild</span></div>
    <nav class="abs main-nav">
      <a href="#">HOME</a><a href="#">ABOUT</a><a href="#">MEMBERS</a><a href="#">RESOURCES</a><a href="#">EVENTS</a><a href="#">MEMBERSHIP</a><a href="#">CONTACT</a>
    </nav>
  </header>

  <section class="abs hero">
    <div class="abs hero-photo" role="img" aria-label="Banner photo of a calm pond covered in lily pads with green trees under a bright sky"></div>
    <p class="abs tagline">Promoting environmental stewardship through<br>operations, research, education &amp; outreach</p>
    <aside class="abs newsletter">
      <h2>Newsletter Sign Up</h2>
      <div class="rule" style="top:69px"></div>
      <p>Neque porro quisquam est qui dolorem ipsum quia dolor sit amet, consectetur</p>
      <div class="field" style="top:136px">Your Name</div>
      <div class="field" style="top:187px">Email Address</div>
      <div class="sign-up">Sign Up</div>
      <div class="rule" style="top:300px"></div>
      <div class="become">BECOME A MEMBER</div>
    </aside>
  </section>

  <main class="abs content">
    <h2 class="section-title" style="left:14px;top:18px">About LSWFSG</h2>
    <p class="about-text">The Lone Star Wetland Flora Stewardship Guild, Inc. is an organization of scientists, educators, students, commercial pesticide applicators, administrators, and concerned individuals interested in the management and study of aquatic plants. The membership reflects a diversity of federal, state, and local agencies; universities and colleges around the world; corporations; and small businesses.</p>
    <div class="read-more">Read More</div>

    <h2 class="section-title" style="left:346px;top:21px">Upcoming Events</h2>
    <div class="event" style="top:79px">
      <div class="thumb" role="img" aria-label="Small photo of a lily pond"></div>
      <h3>2014 Northeast Aquatic Plant</h3>
      <div class="date">January 21, 2014</div>
      <div class="blurb">Lorem Ipsum is simply dummy text of the printing .</div>
    </div>
    <div class="event" style="top:171px">
      <div class="thumb" role="img" aria-label="Small photo of reeds along a pond"></div>
      <h3>2014 Northeast Aquatic Plant</h3>
      <div class="date">January 21, 2014</div>
      <div class="blurb">Lorem Ipsum is simply dummy text of the printing .</div>
    </div>
    <div class="event" style="top:266px">
      <div class="thumb" role="img" aria-label="Small photo of a lily pond"></div>
      <h3>2014 Northeast Aquatic Plant</h3>
      <div class="date">January 21, 2014</div>
      <div class="blurb">Lorem Ipsum is simply dummy text of the printing .</div>
    </div>
    <div class="view-all">View All..</div>

    <div class="ad-slot" role="img" aria-label="Member advertisement: ClearPond Pro algaecide jug and bag by PureMarsh Labs over a blue water background"></div>
  </main>

  <footer>
    <div class="abs copyright">Copyright © 2014 LSWFSG. All rights reserved.</div>
    <a class="abs advertise" href="#">advertise with us</a>
  </footer>
</body>
</html>
```